Förderverein einer Kirchengemeinde sucht Flyer-Design
Zielgruppe
Wir sind ein Förderverein einer Kirchengemeinde, der sich für die kirchenmusikalische Arbeit einsetzt.
Wir wünschen uns ein niveauvolles und zeitgemäßes/modernes Flyerdesign, das die etablierten Konzertbesucher anspricht, aber vor allem auch Menschen erreicht und überzeugt, die (noch) nichts mit Kirche zu tun haben.
Das Alter der (Haupt-) Zielgruppe (Männer und Frauen) erstreckt sich von 45 bis 70 Jahren.
Aufgabenstellung
Bei der Wahl des Formates würden wir (aus der Sicht von Laien) ein zweimal gefaltetes DIN A4 quer Format nehmen. Aber wir lassen uns gerne überraschen und sind grundsätzlich für andere Lösungen offen.
Bitte den Abschnitt für Adress- und sonstige Dateneintragungen samt Kontodaten so gestalten und platzieren, dass man ihn leicht abtrennen und verschicken kann.
Der Flyer soll Kirchenmusik als lebendig und attraktiv darstellen und neue (jüngere) Mitglieder für den Freundeskreis werben.
Lassen Sie die Bilder sprechen!!

```html
<!DOCTYPE html>
<html lang="de">
<head>
<meta charset="utf-8">
<title>Freundeskreis Kirchenmusik – Flyer</title>
<link href="https://fonts.googleapis.com/css2?family=Mulish:ital,wght@0,400;0,600;0,700;0,800;1,400&display=swap" rel="stylesheet">
<style>
:root{
  --bg:#e0e0e0;
  --paper:#ffffff;
  --red:#c1181d;
  --red-dark:#9e1418;
  --ink:#3a3a3a;
  --line:#c8c8c8;
  --bar:#d5d5d5;
  --white:#ffffff;
}
*{box-sizing:border-box;margin:0;padding:0}
html,body{width:1200px;height:954px;overflow:hidden;background:var(--bg);font-family:"Mulish",sans-serif;color:var(--ink)}
.spread{position:absolute;left:30px;width:1138px;height:401px;background:var(--paper);box-shadow:0 1px 4px rgba(0,0,0,.25);overflow:hidden}
.spread--outside{top:43px}
.spread--inside{top:504px}
.abs{position:absolute}
.art{position:absolute;left:0;top:0}

/* form */
.form-title{left:17px;top:10px;font-size:12.5px;font-weight:700;color:var(--red)}
.form-box{left:17px;width:311px;border:1px solid var(--line)}
.form-row{display:flex;border-bottom:1px solid var(--line)}
.form-row:last-child{border-bottom:none}
.form-cell{flex:1;padding:3px 3px;font-size:6.6px;position:relative}
.form-cell + .form-cell{border-left:1px solid var(--line)}
.fill-line{position:absolute;left:3px;right:3px;bottom:3px;border-bottom:1px solid #999}
.section-bar{left:17px;width:311px;height:14px;background:var(--bar);font-size:8.5px;font-weight:600;padding:2px 3px;color:#333}
.check{font-size:7.3px;white-space:nowrap;display:flex;align-items:center;gap:2px}
.check::before{content:"";width:6px;height:6px;border:1px solid #777;display:inline-block;margin-right:1px}
.note{font-size:6.2px;font-style:italic}
.bank{left:17px;top:357px;font-size:6.6px;line-height:11px}
.bank b{font-size:8.5px;font-weight:600;margin-right:4px}
.cut-line{left:341px;top:0;height:401px;border-left:1.5px dashed #555}
.cut-hint{left:333px;top:390px;font-size:4.5px;transform:rotate(-90deg);transform-origin:left top;white-space:nowrap;color:#555}

/* info panel */
.info-panel{left:344px;top:200px;width:225px;height:201px;background:var(--red);color:var(--white)}
.org-line{left:368px;top:213px;font-size:9px;font-weight:700;letter-spacing:.2px;color:var(--white);display:flex;gap:9px;align-items:center}
.org-line .dot{width:7px;height:7px;background:var(--white);border-radius:50%}
.info-text{left:369px;top:243px;font-size:8.5px;line-height:10.6px;color:var(--white);white-space:nowrap}
.info-address{left:393px;top:292px;font-size:9px;font-weight:700;line-height:11.3px;color:var(--white);white-space:nowrap}
.info-more{left:369px;top:361px;font-size:8.5px;line-height:12.2px;color:var(--white);white-space:nowrap}

/* cover */
.cover-claim{left:648px;top:155px;font-size:19.5px;font-weight:600;color:var(--white);white-space:nowrap}
.cover-mark{left:1003px;top:112px;width:90px;height:90px;border-radius:50%;background:var(--white)}
.cover-name{left:960px;width:180px;top:312px;text-align:center;font-size:15.5px;font-weight:800;letter-spacing:1px;line-height:19px;color:var(--white)}

/* inside left */
.headline{left:180px;width:140px;top:46px;text-align:right;font-size:17.5px;font-weight:700;line-height:19.5px;color:var(--red)}
.head-rule{left:329px;top:45px;width:1px;height:84px;background:var(--red)}
.intro{left:337px;top:50px;font-size:10.3px;line-height:14px;white-space:nowrap}
.intro p + p{margin-top:9px}
.sub{left:220px;top:157px;font-size:12.5px;font-weight:700;color:var(--red)}
.benefit{font-size:9.6px;line-height:12.4px;white-space:nowrap}
.benefit b{font-weight:800}

/* inside right */
.reasons-title{left:854px;top:48px;font-size:13px;font-weight:700;color:var(--white);white-space:nowrap}
.reason{font-size:9.6px;line-height:13.4px;color:var(--white);white-space:nowrap}
</style>
</head>
<body>

<!-- Outside: form, info panel, cover -->
<section class="spread spread--outside">
  <svg class="art" width="1138" height="401" viewBox="0 0 1138 401">
    <defs>
      <linearGradient id="organFront" x1="0" y1="0" x2="0" y2="1">
        <stop offset="0" stop-color="#c9a657"/>
        <stop offset=".18" stop-color="#d8c9a3"/>
        <stop offset=".45" stop-color="#a9a6a2"/>
        <stop offset=".62" stop-color="#9b5a52"/>
        <stop offset=".8" stop-color="#b4afa8"/>
        <stop offset="1" stop-color="#d9cdb9"/>
      </linearGradient>
      <linearGradient id="organPipes" x1="0" y1="0" x2="1" y2="1">
        <stop offset="0" stop-color="#8d7a3e"/>
        <stop offset=".14" stop-color="#5e5a4d"/>
        <stop offset=".32" stop-color="#c4c5c2"/>
        <stop offset=".48" stop-color="#8f8e88"/>
        <stop offset=".6" stop-color="#3d3a33"/>
        <stop offset=".78" stop-color="#c39a3a"/>
        <stop offset=".9" stop-color="#e2bf5c"/>
        <stop offset="1" stop-color="#b9a27a"/>
      </linearGradient>
      <linearGradient id="redField" x1="0" y1="0" x2="1" y2="1">
        <stop offset="0" stop-color="#cb1a1f"/><stop offset="1" stop-color="#a31418"/>
      </linearGradient>
    </defs>
    <rect x="344" y="0" width="225" height="200" fill="url(#organFront)" role="img" aria-label="Foto: historischer Orgelprospekt mit vergoldetem Gehäuse"/>
    <rect x="569" y="0" width="460" height="401" fill="url(#organPipes)" role="img" aria-label="Foto: Orgelpfeifen mit vergoldetem Schnitzwerk in Nahaufnahme"/>
    <polygon points="1016,0 1023,0 934,401 927,401" fill="#d9d6d0" opacity=".55"/>
    <polygon points="1023,0 1138,0 1138,401 934,401" fill="url(#redField)"/>
  </svg>

  <h1 class="abs form-title">Beitrittserklärung</h1>
  <div class="abs form-box" style="top:33px;height:109px">
    <div class="form-row" style="height:16px"><div class="form-cell">Name, Vorname</div></div>
    <div class="form-row" style="height:16px"><div class="form-cell">Institution/Firma</div></div>
    <div class="form-row" style="height:31px"><div class="form-cell">Straße, Hausnr., PLZ, Ort<span class="fill-line" style="bottom:15px"></span></div></div>
    <div class="form-row" style="height:16px"><div class="form-cell">Telefon/Mobil</div><div class="form-cell">Geburtsdatum</div></div>
    <div class="form-row" style="height:28px"><div class="form-cell">E-Mail<span class="fill-line"></span></div><div class="form-cell">Datum, Unterschrift<span class="fill-line"></span></div></div>
  </div>

  <div class="abs section-bar" style="top:153px">Mitgliedsbeiträge</div>
  <div class="abs check" style="left:20px;top:176px">Einzelpersonen € 20,-</div>
  <div class="abs check" style="left:20px;top:187px">Ehepaare/Partnerschaften € 32,-</div>
  <div class="abs check" style="left:20px;top:199px">Institutionen/Firmen € 95,-</div>
  <div class="abs note" style="left:28px;top:211px">(jeweils Mindestbeiträge)</div>
  <div class="abs check" style="left:166px;top:176px">Gewünschter Betrag: €<span style="display:inline-block;width:70px;border-bottom:1px solid #999;margin-left:2px;height:7px"></span></div>
  <div class="abs check" style="left:166px;top:191px">Einmalige Spende&nbsp;<i>(ohne Mitgliedschaft)</i></div>
  <div class="abs check" style="left:166px;top:205px">Ich benötige eine Spendenbescheinigung</div>

  <div class="abs section-bar" style="top:230px">SEPA-Lastschriftmandat</div>
  <div class="abs form-box" style="top:244px;height:146px;border-top:none">
    <div class="form-row" style="height:19px"><div class="form-cell" style="flex:0 0 186px">IBAN</div><div class="form-cell">BIC</div></div>
    <div class="form-row" style="height:20px"><div class="form-cell" style="flex:0 0 153px">Kreditinstitut</div><div class="form-cell">Kontoinhaber</div></div>
    <div class="form-row" style="height:47px"><div class="form-cell" style="line-height:8.5px">Hiermit ermächtige ich den Freundeskreis Kirchenmusik den von mir zu entrichtenden<br>Mitgliedsbeitrag von meinem Konto einzuziehen<br><span style="display:block;margin-top:8px">Ort, Datum, Unterschrift</span><span class="fill-line" style="left:95px;bottom:6px"></span></div></div>
    <div class="form-row" style="height:18px"><div class="form-cell note" style="padding-top:4px">Der Einzug der Mitgliedsbeiträge erfolgt zu Beginn eines Kalenderjahres</div></div>
  </div>
  <div class="abs bank"><b>Spendenkonto:</b> Sparkasse Nordheide-Aller<br><span style="padding-left:66px">IBAN: DE00 1234 5678 9012 3456 78</span><br><span style="padding-left:66px">BIC: NOLADE00XYZ</span></div>
  <div class="abs cut-line"></div>
  <div class="abs cut-hint">Hier abtrennen</div>

  <div class="abs info-panel"></div>
  <div class="abs org-line">FREUNDESKREIS <span class="dot"></span> KIRCHENMUSIK</div>
  <p class="abs info-text">Wenn Sie die Kirchenmusik an St. Lamberti<br>als Mitglied im <b>Freundeskreis Kirchenmusik</b><br>fördern möchten, senden Sie die ausgefüllte<br>Beitrittserklärung an den</p>
  <p class="abs info-address">Freundeskreis Kirchenmusik<br>Kirchengemeinde St. Lamberti<br>Lindenstraße 7, 29399 Hollenstedt<br><span style="display:block;margin-top:6px">Tel.: 05123-4567-89<br>info@fk-lamberti.de</span></p>
  <p class="abs info-more">Nähere Informationen finden Sie unter<br><b>www.kirchenmusik-hollenstedt.de</b></p>

  <p class="abs cover-claim">Kirchenmusik braucht Freunde…</p>
  <div class="abs cover-mark"></div>
  <p class="abs cover-name">FREUNDESKREIS<br>KIRCHENMUSIK</p>
</section>

<!-- Inside: benefits and reasons -->
<section class="spread spread--inside">
  <svg class="art" width="1138" height="401" viewBox="0 0 1138 401">
    <defs>
      <linearGradient id="redField2" x1="0" y1="0" x2="1" y2="1">
        <stop offset="0" stop-color="#cb1a1f"/><stop offset="1" stop-color="#a31418"/>
      </linearGradient>
      <linearGradient id="trumpet" x1="0" y1="0" x2="1" y2="1">
        <stop offset="0" stop-color="#d1ad5e"/><stop offset=".35" stop-color="#a99a80"/><stop offset=".6" stop-color="#c89c86"/><stop offset="1" stop-color="#595a55"/>
      </linearGradient>
      <linearGradient id="flutes" x1="0" y1="0" x2="0" y2="1">
        <stop offset="0" stop-color="#556347"/><stop offset=".35" stop-color="#d7d6d2"/><stop offset=".65" stop-color="#8fa3b8"/><stop offset="1" stop-color="#4c5a34"/>
      </linearGradient>
      <linearGradient id="kids" x1="0" y1="0" x2="0" y2="1">
        <stop offset="0" stop-color="#3d5a2a"/><stop offset=".4" stop-color="#e3c93a"/><stop offset=".7" stop-color="#b8b39a"/><stop offset="1" stop-color="#6e8a3e"/>
      </linearGradient>
      <linearGradient id="brass" x1="0" y1="0" x2="0" y2="1">
        <stop offset="0" stop-color="#c9c6bd"/><stop offset=".45" stop-color="#e9e8e4"/><stop offset=".75" stop-color="#5b5850"/><stop offset="1" stop-color="#9d9a90"/>
      </linearGradient>
      <linearGradient id="choir" x1="0" y1="0" x2="0" y2="1">
        <stop offset="0" stop-color="#d5b9a4"/><stop offset=".3" stop-color="#8c7467"/><stop offset=".55" stop-color="#2c2624"/><stop offset="1" stop-color="#1c1817"/>
      </linearGradient>
    </defs>
    <polygon points="0,0 154,0 180,117 0,117" fill="url(#trumpet)" role="img" aria-label="Foto: Hände an einer Trompete"/>
    <polygon points="0,119 181,119 212,262 0,262" fill="url(#flutes)" role="img" aria-label="Foto: Flötenensemble mit Blockflöten im Garten"/>
    <polygon points="0,264 213,264 243,401 0,401" fill="url(#kids)" role="img" aria-label="Foto: Kinderchor in gelben T-Shirts"/>
    <polygon points="154,0 160,0 249,401 243,401" fill="#d9d6d0" opacity=".6"/>
    <polygon points="569,0 822,0 866,199 569,199" fill="url(#brass)" role="img" aria-label="Foto: Posaunenchor mit Blechblasinstrumenten vor der Kirche"/>
    <polygon points="569,201 866,201 911,401 569,401" fill="url(#choir)" role="img" aria-label="Foto: Kantorei im Konzert in der Kirche"/>
    <polygon points="816,0 822,0 911,401 905,401" fill="#d9d6d0" opacity=".55"/>
    <polygon points="822,0 1138,0 1138,401 911,401" fill="url(#redField2)"/>
    <line x1="569" y1="0" x2="569" y2="401" stroke="#bdbdbd" stroke-width="1"/>
  </svg>

  <h2 class="abs headline">Kirchenmusik braucht Freunde</h2>
  <div class="abs head-rule"></div>
  <div class="abs intro">
    <p>Im Jahr 1999 gegründet, unterstützt<br>der Freundeskreis Kirchenmusik die<br>vielfältigen musikalischen Aktivitäten<br>an der St. Lamberti-Kirche.</p>
    <p>Wir laden Sie ein, Mitglied zu werden!</p>
  </div>

  <h3 class="abs sub">Mit Ihrem Beitrag …</h3>
  <p class="abs benefit" style="left:223px;top:186px">…bereichern Sie Hollenstedts kulturelle Landschaft durch den Erhalt<br>&nbsp;&nbsp;&nbsp;&nbsp;und Ausbau unseres hohen kirchenmusikalischen Niveaus</p>
  <p class="abs benefit" style="left:231px;top:219px">…stärken Sie das Ehrenamt</p>
  <p class="abs benefit" style="left:237px;top:241px">…ermöglichen Sie der <b>Kantorei</b>, dem <b>Posaunenchor</b>, dem<br>&nbsp;&nbsp;&nbsp;&nbsp;<b>Kinderchor</b> und dem <b>Flötenensemble</b> regelmäßige Proben-<br>&nbsp;&nbsp;&nbsp;&nbsp;arbeit, Probenwochenenden und die Anschaffung von<br>&nbsp;&nbsp;&nbsp;&nbsp;Notenmaterial</p>
  <p class="abs benefit" style="left:250px;top:299px">…erhalten Sie die historische <b>Johann Brockmann Orgel von 1748</b></p>
  <p class="abs benefit" style="left:254px;top:320px">…fördern Sie die Ausbildung kirchenmusikalischen Nach-<br>&nbsp;&nbsp;&nbsp;&nbsp;wuchses</p>

  <h3 class="abs reasons-title">Mitglieder haben gute Gründe:</h3>
  <p class="abs reason" style="left:864px;top:83px">Sie…</p>
  <p class="abs reason" style="left:869px;top:107px">…erhalten ermäßigte Eintrittspreise von<br>&nbsp;&nbsp;&nbsp;&nbsp;gemeindeeigenen Konzerten</p>
  <p class="abs reason" style="left:880px;top:148px">…können Konzertkarten vor dem öffentlichen<br>&nbsp;&nbsp;&nbsp;&nbsp;Verkauf erwerben</p>
  <p class="abs reason" style="left:889px;top:189px">…gestalten die Arbeit des Freundeskreises<br>&nbsp;&nbsp;&nbsp;&nbsp;in den jährlichen Mitgliederversammlungen<br>&nbsp;&nbsp;&nbsp;&nbsp;aktiv mit</p>
  <p class="abs reason" style="left:903px;top:244px">…erhalten aktuelle Informationen über<br>&nbsp;&nbsp;&nbsp;&nbsp;Veranstaltungen der Gemeinde bequem<br>&nbsp;&nbsp;&nbsp;&nbsp;per Email und profitieren so zu allererst</p>
  <p class="abs reason" style="left:916px;top:298px">…können den Mitgliedsbeitrag steuerlich<br>&nbsp;&nbsp;&nbsp;&nbsp;absetzen und erhalten eine Spenden-<br>&nbsp;&nbsp;&nbsp;&nbsp;bescheinigung</p>
</section>

</body>
</html>
```